Zelvo Stationary

Design the stationary of Zelvo Promotions Group.

Zelvo is a BTL company, BTL meaning "below the line". In other words Zelvo is a Promotional Marketing company (the company that design the brands promotional activities).

The design should transmit creativity, agility, boldness.

I need:
* Bis Card
* Letter head
* Envelopes, both vertical and horizontal (for legal size), and letter envelope
* Folders
* PPT template (Title page and regular page)
* CD slip (CD envelope)
* ID card (employee card)

And what ever else you want to throw in.
Updates

Guys,

Something I missed from the brief.   The predominat color should be RED.

Also, have fun and play with the exclamation mark (!) of the logo. 

Hi guys, more comments:

Remember that Zelvo is a "creativity" agency, not in the advertising side but on the promotional side, and that should reflect on the stationary.

 I want a bold design.  Bold and yet crisp.

 

Guys, i just uploaded the Logo in AI format.

I Also uploaded the actual Zelvo Bis Card, wich I like.  So I will like to see some designs with that bis card approach.

Guys, I am so sorry, but I notice in your last post that I upladed a wrong design ("13154_promotions_group_zelvo_brief225630.ai").  The problem was that I asked the designer the file in AI format and he send me thw wrong file, and since I dont have Illustrator I could not verify it.

The differences are minor, I just already ask him the correct one (similar to the EPS file).

Sorry                                   

Just post the correct AI file : "Zelvo Logo.ai"

Reason: I'm expecting more designs to choose from and also I wont be available tomorrow to decide.

Reason: Sorry guys, but we are not there yet!

Target Market(s)

Marketing directors, Marketing Managers

Industry/Entity Type

Legal

Requirements
Must have
• Must work with the logo attached.
The predominat color should be RED.
Play and have fun with the exclamation mark (!).
Should not have
• * No old fonts

Should not be:
* boring
* Informal
* rigid

```html
<!DOCTYPE html>
<html lang="en">
<head>
<meta charset="utf-8">
<title>Zelvo Promotions Group — Business Card</title>
<link rel="stylesheet" href="https://fonts.googleapis.com/css2?family=PT+Sans:wght@400;700&display=swap">
<style>
  :root {
    --zelvo-red: #d11f26;
    --zelvo-red-deep: #b8171d;
    --ink: #111111;
    --ink-soft: #3a3a3a;
    --muted: #6a6a6a;
    --paper-light: #fafafa;
    --paper-grey: #c9c9c9;
    --stage: #2b2b2b;
    --white: #ffffff;
  }
  * { box-sizing: border-box; margin: 0; padding: 0; }
  html, body { width: 900px; height: 1200px; overflow: hidden; }
  body {
    position: relative;
    background: var(--stage);
    font-family: "PT Sans", "Helvetica Neue", Arial, sans-serif;
  }

  .card {
    position: absolute;
    left: 108px;
    width: 690px;
    height: 405px;
    overflow: hidden;
  }

  /* ---------- Front ---------- */
  .card--front { top: 90px; background: var(--zelvo-red); }
  .front-pattern {
    position: absolute; inset: 0;
    background: radial-gradient(ellipse at 50% 45%, var(--zelvo-red) 0%, var(--zelvo-red-deep) 100%);
  }
  .wordmark { position: absolute; font-weight: 700; line-height: 1; }
  .wordmark__name { display: block; letter-spacing: -1px; }
  .wordmark__line { display: block; text-transform: uppercase; }
  .card--front .wordmark { left: 148px; top: 118px; color: var(--white); }
  .card--front .wordmark__name { font-size: 92px; }
  .card--front .wordmark__line { font-size: 19px; letter-spacing: 5.2px; margin-top: 4px; }
  .mark-dot { position: absolute; border-radius: 50%; }
  .card--front .mark-dot {
    left: 448px; top: 198px; width: 46px; height: 46px;
    background: var(--white);
  }

  /* ---------- Back ---------- */
  .card--back {
    top: 668px;
    background: radial-gradient(circle at 48% 45%, var(--paper-light) 0%, #ececec 40%, var(--paper-grey) 100%);
  }
  .back-corner {
    position: absolute; left: 0; top: 0; width: 120px; height: 92px;
    background: var(--zelvo-red);
  }
  .back-rail {
    position: absolute; left: 0; top: 202px; width: 120px; height: 203px;
    background: var(--zelvo-red);
  }
  .back-divider {
    position: absolute; left: 120px; top: 0; width: 5px; height: 405px;
    background: var(--white);
  }
  .card--back .wordmark { left: 14px; top: 92px; color: var(--ink); }
  .card--back .wordmark__name { font-size: 72px; }
  .card--back .wordmark__line { font-size: 15px; letter-spacing: 4.2px; margin-top: 2px; }
  .card--back .mark-dot {
    left: 262px; top: 140px; width: 36px; height: 36px;
    background: var(--zelvo-red);
  }

  .person { position: absolute; right: 41px; top: 110px; text-align: right; }
  .person__name { font-size: 26px; font-weight: 700; color: var(--ink); line-height: 1.1; }
  .person__role { font-size: 19px; color: var(--muted); margin-top: 4px; }

  .address {
    position: absolute; left: 132px; top: 201px;
    font-size: 13px; line-height: 16px; color: var(--ink-soft);
  }

  .contact-list { position: absolute; left: 0; top: 238px; width: 690px; list-style: none; }
  .contact {
    position: relative; height: 34px;
    display: flex; align-items: center;
  }
  .contact__icon {
    position: absolute; left: 88px; top: 5px; width: 24px; height: 24px;
  }
  .contact__value {
    position: absolute; left: 127px; right: 0; top: 2px; height: 31px;
    padding-left: 9px; display: flex; align-items: center;
    font-size: 16.5px; color: var(--ink-soft);
  }
  .contact--band .contact__value { background: var(--ink); color: var(--white); }
</style>
</head>
<body>

  <section class="card card--front" aria-label="Business card front">
    <div class="front-pattern" role="img" aria-label="Faint repeating exclamation-mark pattern in deeper red"></div>
    <div class="wordmark">
      <span class="wordmark__name">zelvo</span>
      <span class="wordmark__line">Promotions Group</span>
    </div>
    <span class="mark-dot" aria-hidden="true"></span>
  </section>

  <section class="card card--back" aria-label="Business card back">
    <div class="back-corner"></div>
    <div class="back-rail"></div>
    <div class="back-divider"></div>

    <div class="wordmark">
      <span class="wordmark__name">zelvo</span>
      <span class="wordmark__line">Promotions Group</span>
    </div>
    <span class="mark-dot" aria-hidden="true"></span>

    <div class="person">
      <p class="person__name">Mara Quint</p>
      <p class="person__role">Creative Director</p>
    </div>

    <address class="address" style="font-style:normal">
      Street, Region, Country<br>PO BOX 321
    </address>

    <ul class="contact-list">
      <li class="contact contact--band">
        <svg class="contact__icon" viewBox="0 0 24 24" aria-hidden="true">
          <rect x="6" y="1.5" width="12" height="21" rx="2" fill="none" stroke="#fff" stroke-width="2"/>
          <rect x="8.5" y="5" width="7" height="11" fill="#fff"/>
          <circle cx="12" cy="19" r="1.3" fill="#fff"/>
        </svg>
        <span class="contact__value">+94 700 555 019</span>
      </li>
      <li class="contact">
        <svg class="contact__icon" viewBox="0 0 24 24" aria-hidden="true">
          <path d="M2 9c0-3 4-5 10-5s10 2 10 5v1.5h-5V8.5c-1.5-.7-8.5-.7-10 0v2H2z" fill="#fff"/>
          <path d="M5 12h14l2 8H3z" fill="#fff"/>
          <circle cx="12" cy="15.8" r="2.4" fill="#d11f26"/>
        </svg>
        <span class="contact__value">+94 110 555 204</span>
      </li>
      <li class="contact contact--band">
        <svg class="contact__icon" viewBox="0 0 24 24" aria-hidden="true">
          <rect x="1.5" y="5" width="21" height="14" fill="#fff"/>
          <path d="M1.5 5l10.5 8 10.5-8" fill="none" stroke="#d11f26" stroke-width="1.6"/>
        </svg>
        <span class="contact__value">mquint@zelvopromotions.com</span>
      </li>
      <li class="contact">
        <svg class="contact__icon" viewBox="0 0 24 24" aria-hidden="true">
          <circle cx="11" cy="11" r="9" fill="none" stroke="#fff" stroke-width="2"/>
          <ellipse cx="11" cy="11" rx="4" ry="9" fill="none" stroke="#fff" stroke-width="1.6"/>
          <path d="M2 11h18M4 6h14M4 16h14" stroke="#fff" stroke-width="1.6"/>
          <path d="M13 13l9 3.5-3.5 1.2 2.5 3-1.5 1.2-2.5-3-2 2.6z" fill="#fff" stroke="#d11f26" stroke-width="0.8"/>
        </svg>
        <span class="contact__value">www.zelvopromotions.com</span>
      </li>
    </ul>
  </section>

</body>
</html>
```